Exciting & Elegant Stationary Pack

Stationary consists of
1. Letter head / Envelope
2. Business Card
3. Invoice
4. 40x40mm sticker

Attached files;

1. Logo (Other formats available on request)
2. MS word Doc - For information and description of design
3. Website image (This will be our new website so use the colours so everything ties together)
4. Sample of stationary pack we like, but feel free to be creative

Target Market(s)

Home improvement

Industry/Entity Type

Construction

Font styles to use
Other font styles liked:
• Leave up to designer - We like font used on (website attached image)

Requirements
Must have
• Please look at uploaded file of sample website and use colours
Nice to have
• Any type of business card design - eg. metal, die cut, embossed, etc...

```html
<!DOCTYPE html>
<html lang="en">
<head>
<meta charset="utf-8">
<title>Grout &amp; Co — Business Card</title>
<link rel="stylesheet" href="https://fonts.googleapis.com/css2?family=Open+Sans:wght@400;700&display=swap">
<style>
  :root {
    --backdrop: #6a6a6a;
    --navy: #0d3f68;
    --orange: #f08a2e;
    --white: #ffffff;
    --marble-light: #f4f4f2;
    --marble-vein: #d9dad8;
  }
  * { margin: 0; padding: 0; box-sizing: border-box; }
  html, body {
    width: 1200px;
    height: 750px;
    overflow: hidden;
    background: var(--backdrop);
    font-family: "Open Sans", sans-serif;
  }
  .canvas { position: relative; width: 1200px; height: 750px; }

  .card {
    position: absolute;
    width: 461px;
    height: 263px;
    box-shadow: 0 8px 10px rgba(0, 0, 0, 0.35);
  }

  /* Front: contact side */
  .card--front { left: 308px; top: 105px; background: var(--navy); }
  .card--front .card__frame {
    position: absolute;
    inset: 8px;
    border: 2px solid var(--orange);
  }
  .contact {
    position: absolute;
    left: 0; right: 0; top: 72px;
    text-align: center;
    color: var(--white);
  }
  .contact__name {
    color: var(--orange);
    font-weight: 700;
    font-size: 18px;
    line-height: 20px;
    letter-spacing: 0.3px;
  }
  .contact__role { font-size: 13.5px; line-height: 17px; }
  .contact__divider {
    width: 192px;
    margin: 6px auto;
    border-top: 2px dotted rgba(255, 255, 255, 0.85);
  }
  .contact__licence { font-size: 13px; line-height: 18px; padding: 3px 0; }
  .contact__lines { margin-top: 8px; font-size: 13px; line-height: 17.5px; }
  .contact__label { color: var(--orange); font-weight: 700; }

  /* Back: brand side */
  .card--back { left: 475px; top: 412px; overflow: hidden; }
  .card__marble {
    position: absolute;
    inset: 0;
    background: linear-gradient(150deg, var(--marble-light) 0%, var(--marble-vein) 35%, var(--marble-light) 55%, var(--marble-vein) 80%, var(--marble-light) 100%);
  }
  .card--back .card__frame {
    position: absolute;
    inset: 8px;
    border: 2px solid var(--navy);
  }
  .brand {
    position: absolute;
    left: 0; right: 0; top: 0; bottom: 0;
    display: flex;
    align-items: center;
    justify-content: center;
    gap: 10px;
  }
  .brand__mark { width: 22px; height: 22px; background: var(--navy); }
  .brand__name {
    color: var(--navy);
    font-weight: 700;
    font-size: 30px;
    letter-spacing: 1px;
  }
</style>
</head>
<body>
<main class="canvas">
  <section class="card card--front">
    <div class="card__frame"></div>
    <div class="contact">
      <p class="contact__name">LIAM PORTER</p>
      <p class="contact__role">PROJECT MANAGER</p>
      <div class="contact__divider"></div>
      <p class="contact__licence">Lic No.,204518k</p>
      <div class="contact__divider"></div>
      <div class="contact__lines">
        <p><span class="contact__label">C :</span> 0400 318 275</p>
        <p>hello@groutandco.com.au</p>
        <p>www.groutandco.com.au</p>
      </div>
    </div>
  </section>

  <section class="card card--back">
    <div class="card__marble" role="img" aria-label="White marble stone texture with soft grey veins"></div>
    <div class="card__frame"></div>
    <div class="brand">
      <span class="brand__mark"></span>
      <span class="brand__name">GROUT &amp; CO</span>
    </div>
  </section>
</main>
</body>
</html>
```